4th Generation Family Business Needs a New Card Design!

We are a family owned 4th Generation company. We are based in the Sydney, Australia area and we are desperately in need of a more modern and classy card. We are monumental masons who design, supply & erect lasting memorials throughout cemeteries in Sydney. Our customers are normally in a period of grieving. I have attached logo files that will need to be implemented on the card. Company was established 1935. Australian Owned and Operated. Card needs to be designed to PIXO.com specification.

Target Market(s)

Our target market is based upon people that a grieving for family members that have passed away. We also deal with alot of companies that own and operate cemeteries.

Industry/Entity Type

Business

Contact Information for Business Card

Simon Harcourt, Operations Manager, 0417293086, simon@harcourtmemorials.com.au
Lewis Harcourt, Director, 0491630572, lewis@harcourtmemorials.com.au
Phone # 02 9561 3048
Website: www.harcourtmemorials.com.au
Address: Suite 17, 8 Palfrey Lane, West Carlow, Sydney NSW 2156

Font styles to use
Serif
Decorative
Script

Requirements
Must have
• Would like to see the logo nicely implemented with a modern design. Embossed lettering would be a nice additive.

```html
<!DOCTYPE html>
<html lang="en">
<head>
<meta charset="utf-8">
<title>Harcourt Memorials – Business Card</title>
<link rel="stylesheet" href="https://fonts.googleapis.com/css2?family=Cinzel:wght@400;600&family=Open+Sans:wght@400;600&display=swap">
<style>
  :root {
    --bg: #e6e6e6;
    --card: #ffffff;
    --gold: #f0c02c;
    --gold-dark: #d9a918;
    --ink: #1e1e1e;
    --grey: #6d6d6d;
    --rule: #3a3a3a;
  }
  * { margin: 0; padding: 0; box-sizing: border-box; }
  html, body { width: 1200px; height: 950px; overflow: hidden; }
  body {
    background: var(--bg);
    font-family: "Open Sans", Arial, sans-serif;
    position: relative;
  }
  .card {
    position: absolute;
    left: 250px;
    width: 700px;
    height: 400px;
    background: var(--card);
    box-shadow: 0 4px 14px rgba(0,0,0,.18);
    overflow: hidden;
  }
  .card--front { top: 50px; }
  .card--back { top: 500px; }

  .brand {
    position: absolute;
    left: 0; right: 0;
    text-align: center;
    font-family: "Cinzel", Georgia, serif;
    font-weight: 600;
    color: var(--ink);
    letter-spacing: 2px;
    line-height: 1;
  }
  .card--front .brand { top: 160px; font-size: 46px; }
  .card--back .brand { top: 198px; font-size: 28px; }

  .band {
    position: absolute;
    inset: 0;
    width: 700px;
    height: 400px;
  }
  .person {
    position: absolute;
    top: 60px;
    left: 0; right: 0;
    text-align: center;
    font-family: "Cinzel", Georgia, serif;
    color: var(--ink);
  }
  .person__name { font-size: 26px; font-weight: 600; letter-spacing: 1px; line-height: 1.2; }
  .person__role { font-size: 15px; font-weight: 400; letter-spacing: 1px; margin-top: 2px; line-height: 1.2; }

  .contact {
    position: absolute;
    top: 268px;
    left: 0; right: 0;
    text-align: center;
    color: var(--grey);
    font-size: 15px;
    line-height: 26px;
  }
  .contact__row { display: flex; justify-content: center; align-items: center; gap: 6px; }
  .contact__icon { width: 14px; height: 14px; fill: var(--ink); }
  .contact__web { display: block; color: var(--ink); font-weight: 600; }
  .contact__web span { color: var(--gold-dark); }
</style>
</head>
<body>
  <section class="card card--front">
    <div class="brand">Harcourt Memorials</div>
  </section>

  <section class="card card--back">
    <svg class="band" viewBox="0 0 700 400" aria-hidden="true">
      <path d="M0 0 H700 V125 Q360 145 0 205 Z" fill="var(--gold)"/>
      <path d="M0 205 Q360 145 700 125" fill="none" stroke="var(--rule)" stroke-width="3"/>
    </svg>
    <div class="person">
      <div class="person__name">Simon Harcourt</div>
      <div class="person__role">Operations Manager</div>
    </div>
    <div class="brand">Harcourt Memorials</div>
    <div class="contact">
      <div class="contact__row">Suite 17, 8 Palfrey Lane, West Carlow, Sydney NSW 2156</div>
      <div class="contact__row">
        <svg class="contact__icon" viewBox="0 0 24 24"><path d="M6.6 10.8a15 15 0 0 0 6.6 6.6l2.2-2.2c.3-.3.7-.4 1-.2 1.1.4 2.3.6 3.6.6.6 0 1 .4 1 1V20c0 .6-.4 1-1 1A17 17 0 0 1 3 4c0-.6.4-1 1-1h3.5c.6 0 1 .4 1 1 0 1.3.2 2.5.6 3.6.1.3 0 .7-.2 1z"/></svg>
        <span>02 9561 3048</span>
        <svg class="contact__icon" viewBox="0 0 24 24"><path d="M7 1h10a2 2 0 0 1 2 2v18a2 2 0 0 1-2 2H7a2 2 0 0 1-2-2V3a2 2 0 0 1 2-2zm0 3v15h10V4z"/></svg>
        <span>0417293086</span>
        <svg class="contact__icon" viewBox="0 0 24 24"><path d="M2 5h20v14H2zm2 2v.5l8 5 8-5V7zm0 2.8V17h16V9.8l-8 5z"/></svg>
        <span>simon@harcourtmemorials.com.au</span>
      </div>
      <div class="contact__web">www.<span>harcourtmemorials</span>.com.au</div>
    </div>
  </section>
</body>
</html>
```